Etiketten für Olivenöl-Intensivcreme
Zielgruppe
Wir produzieren Bio-Food, u.a. Wein und Olivenöl. Jetzt soll eine Olivenöl-Intensivcreme im Bereich Kosmetik auf dem Markt platziert werden. Unsere Zielgruppe hat ein sehr breites Altersspektrum (jung bis alt), ist naturverbunden, tierlieb, gebildet, kritisch-reflektierend, weiß gute Qualität zu schätzen, ist überwiegend weiblich. Die Olivenöl-Intensivcreme hat eine sehr breite Verwendung und soll sich als 'Allzweckwaffe' in jedem Haushalt etablieren (Babyhaut-Pflege, Lippenpflege, Ganzkörperpflege, Hand-Schutzcreme etc.).
Aufgabenstellung
Die Creme soll heißen: Velamira (es könnte z.B. der Buchstabe 'O' durch eine Olive ersetzt werden). Es gibt zwei Etikette (Deckeloberseite der Metalldose und auf dem Boden). Der Durchmesser der Etikette ist jeweils 5,5 cm. Die Deckelunterseite gilt reinen Pflichtangaben. Im Dateidownloadbereich sind die Textvorgaben für die Etikette. MUT zur Farbe! Wir sind NICHT brav und angepasst! Orange kann Akzente setzen bzw. für Aufmerksamkeit im Regal sorgen.

```html
<!DOCTYPE html>
<html lang="de">
<head>
<meta charset="utf-8">
<title>Velamira – Etiketten</title>
<link rel="stylesheet" href="https://fonts.googleapis.com/css2?family=Josefin+Sans:wght@400;600&family=Kaushan+Script&display=swap">
<style>
  :root {
    --forest: #0f3b32;
    --olive: #a8a01a;
    --olive-soft: #c9c25a;
    --leaf: #5c8a4a;
    --paper: #ffffff;
    --backdrop: #d9d9d9;
  }
  * { margin: 0; padding: 0; box-sizing: border-box; }
  html, body { width: 1200px; height: 1200px; overflow: hidden; background: var(--backdrop); }
  .canvas { position: relative; width: 1200px; height: 1200px; }
  .label {
    position: absolute; top: 330px; width: 540px; height: 540px;
    border-radius: 50%; background: var(--paper); overflow: hidden;
    font-family: "Josefin Sans", sans-serif; font-variant: small-caps;
  }
  .label--lid { left: 30px; }
  .label--base { left: 630px; }
  .label svg.frame { position: absolute; inset: 0; }
  .line {
    position: absolute; left: 50%; transform: translate(-50%, -50%);
    white-space: nowrap; text-align: center; line-height: 1;
  }
  .brand { color: var(--olive); font-size: 21px; letter-spacing: .5px; font-variant: normal; text-transform: uppercase; }
  .brand-dot { position: absolute; left: 50%; top: 88px; width: 20px; height: 20px; margin-left: -10px; border: 2px solid var(--olive); border-radius: 50%; }
  .wordmark { font-family: "Kaushan Script", cursive; font-variant: normal; color: var(--forest); }
  .wordmark--lid { top: 222px; font-size: 70px; }
  .wordmark--base { top: 75px; font-size: 60px; }
  .product-box {
    position: absolute; left: 50%; top: 265px; width: 232px; height: 112px; margin-left: -116px;
    border: 3px solid var(--olive); padding: 5px;
  }
  .product-box__fill {
    background: var(--olive); color: var(--paper); height: 60px;
    display: flex; flex-direction: column; justify-content: center; align-items: center;
    font-size: 24px; line-height: 1.05;
  }
  .product-box__sub { color: var(--olive); font-size: 24px; text-align: center; margin-top: 9px; }
  .claim { color: var(--forest); font-size: 24px; }
  .seal { position: absolute; left: 375px; top: 382px; width: 88px; height: 88px; border-radius: 50%; background: var(--forest); border: 3px solid var(--paper); }
  .tagline-box {
    top: 130px; border: 2px solid var(--olive); padding: 3px;
  }
  .tagline-box span { display: block; background: var(--olive); color: var(--paper); font-size: 19px; padding: 6px 10px 4px; }
  .info { color: var(--forest); font-size: 19px; }
  .info u { text-underline-offset: 2px; }
  .maker { color: var(--olive); font-size: 16.5px; }
  .volume { color: var(--olive); }
  .legal { color: var(--forest); font-size: 16px; }
  .recycle-mark { position: absolute; left: 85px; top: 370px; width: 42px; height: 42px; border-radius: 50%; background: var(--olive); }
</style>
</head>
<body>
<main class="canvas">

  <section class="label label--lid" aria-label="Deckeletikett">
    <svg class="frame" width="540" height="540" viewBox="0 0 540 540">
      <defs>
        <radialGradient id="wreath-tone" cx="50%" cy="50%" r="50%">
          <stop offset="0.78" stop-color="#7fa35f"/>
          <stop offset="0.88" stop-color="#a9c07a"/>
          <stop offset="1" stop-color="#dfe6c8"/>
        </radialGradient>
      </defs>
      <circle cx="270" cy="270" r="262" fill="url(#wreath-tone)" role="img" aria-label="Kranz aus Olivenzweigen mit Blättern und grünen Oliven"/>
      <circle cx="270" cy="270" r="210" fill="var(--paper)" stroke="var(--forest)" stroke-width="7"/>
      <circle cx="270" cy="270" r="198" fill="none" stroke="var(--olive)" stroke-width="2"/>
    </svg>
    <span class="brand-dot"></span>
    <p class="line brand" style="top:158px">Kalven.land</p>
    <h1 class="line wordmark wordmark--lid">Velamira</h1>
    <div class="product-box">
      <div class="product-box__fill"><span>Olivenöl</span><span>Intensivcreme</span></div>
      <p class="product-box__sub">Naturkosmetik</p>
    </div>
    <p class="line claim" style="top:417px">Pflege- und</p>
    <p class="line claim" style="top:442px">Schutzcreme</p>
    <span class="seal" role="img" aria-label="Siegel"></span>
  </section>

  <section class="label label--base" aria-label="Bodenetikett">
    <h2 class="line wordmark wordmark--base">Velamira</h2>
    <p class="line tagline-box"><span>Wasserfreie Creme, unparfümiert</span></p>
    <p class="line info" style="top:174px"><u>Ingredients:</u> Olea Europaea Fruit Oil,</p>
    <p class="line info" style="top:198px">Hydrogenated Rapeseed Oil, Tocopherol</p>
    <p class="line info" style="top:230px"><u>Anwendung:</u> Sparsam auf die trockene</p>
    <p class="line info" style="top:254px">Haut auftragen (ergiebig!). Die Einwirkzeit</p>
    <p class="line info" style="top:279px">kann einige Minuten dauern, vorher kann es</p>
    <p class="line info" style="top:304px">beim Berühren von Gegenständen mit den</p>
    <p class="line info" style="top:328px">gecremten Körperpartien</p>
    <p class="line info" style="top:352px">zur Fettübertragung kommen.</p>
    <span class="recycle-mark"></span>
    <p class="line maker" style="top:382px">Kalven.land</p>
    <p class="line maker" style="top:402px">Dr. med. Lena Holmer</p>
    <p class="line maker" style="top:422px">Hafenweg 12 · D-24000 Norderau</p>
    <p class="line maker" style="top:442px">www.kalven.land</p>
    <p class="line volume" style="top:384px; left:456px; font-size:30px">150</p>
    <p class="line volume" style="top:408px; left:456px; font-size:20px">ml</p>
    <p class="line legal" style="top:472px">Mind. haltbar: Januar 2021</p>
    <p class="line legal" style="top:492px">Made in Germany</p>
  </section>

</main>
</body>
</html>
```